Stationery design for software development / consultancy company

We need stationary design based on company logo.

We are based in London, UK and we are providing integration solutions development / consultancy services for KVT integration projects across UK.

Our name refers two words - integration and grace - and it shows our clients our main specialization field and key characteristics of our solutions / products. We also would like to be associated with follow words: smart, reliable, unique.

Project delivery should include:
- Powerpoint template (needs to have a Cover Page, Table of Contents, 1-2 sample pages, and a Closing/Summary slide at the end)
- Letterhead A4 (Word template)
- Standard invoice A4 (Word template)
- With Compliments Slips A5 (Word template)
- Business card (adobe illustrator)

Attached is logo in vector (please use logo with white background!) and company details for printed stationery.

highly skilled IT professionals

Software

• Clear background in all A4/A5 documents.
All text should be editable, i.e. I will need sources.
• I would prefer light, web 2.0 style colours, follow are in my main interest:
- combination of light grey and orange
- Logo colours
• Please no watermarks on printed stationary

```html
<!DOCTYPE html>
<html lang="en">
<head>
<meta charset="utf-8">
<title>Corvella Business Card</title>
<link href="https://fonts.googleapis.com/css2?family=Open+Sans:wght@400;600;700&display=swap" rel="stylesheet">
<style>
  :root {
    --stage: #4a4a4a;
    --card: #ffffff;
    --accent: #fbb043;
    --ink: #555555;
    --ink-soft: #6a6a6a;
    --rule: #8a8a8a;
    --mark: #1ba7dc;
  }
  * { margin: 0; padding: 0; box-sizing: border-box; }
  html, body { width: 1200px; height: 900px; overflow: hidden; }
  body {
    background: var(--stage);
    font-family: "Open Sans", Arial, sans-serif;
    position: relative;
  }
  .card {
    position: absolute;
    left: 220px;
    width: 776px;
    background: var(--card);
  }
  .card--front { top: 32px; height: 398px; }
  .card--back { top: 472px; height: 400px; }
  .band-top {
    position: absolute; left: 0; top: 0; width: 100%;
    background: var(--accent);
    color: #fff;
  }
  .card--front .band-top { height: 72px; }
  .card--back .band-top { height: 74px; }
  .band-bottom {
    position: absolute; left: 0; bottom: 0; width: 100%; height: 22px;
    background: var(--accent);
  }
  .holder-name {
    position: absolute; left: 48px; top: 20px;
    font-weight: 700; font-size: 21px; letter-spacing: 0.5px;
  }
  .holder-role {
    position: absolute; left: 100px; top: 44px;
    font-size: 14px;
  }
  .web {
    font-weight: 700; font-size: 19px;
  }
  .card--front .web { position: absolute; right: 52px; top: 24px; }
  .card--back .web {
    position: absolute; left: 0; width: 100%; top: 24px; text-align: center;
  }
  .brand {
    position: absolute;
    display: flex; align-items: center; gap: 14px;
    color: var(--ink);
  }
  .brand-dot { width: 44px; height: 44px; border-radius: 50%; background: var(--mark); }
  .brand-name { font-weight: 600; font-size: 54px; letter-spacing: -0.5px; line-height: 1; }
  .card--front .brand { left: 50px; top: 160px; }
  .card--back .brand { left: 0; width: 100%; justify-content: center; top: 194px; }
  .divider {
    position: absolute; left: 412px; top: 132px;
    width: 2px; height: 198px; background: var(--rule);
  }
  .contact {
    position: absolute; left: 446px; top: 128px;
    font-size: 15px; line-height: 19.5px; color: var(--ink-soft);
  }
  .contact address { font-style: normal; margin-bottom: 18px; }
</style>
</head>
<body>
  <section class="card card--front">
    <header class="band-top">
      <div class="holder-name">DANIEL HARCOURT</div>
      <div class="holder-role">Director</div>
      <div class="web">Web : www.corvella.co.uk</div>
    </header>
    <div class="brand">
      <span class="brand-dot"></span>
      <span class="brand-name">corvella</span>
    </div>
    <div class="divider"></div>
    <div class="contact">
      <address>
        Corvella Limited<br>
        42 Marlow Court<br>
        88 Fenwick Lane<br>
        London<br>
        SW9 4QT<br>
        United Kingdom
      </address>
      <div>Mob : +44(0)7700900418</div>
      <div>Tel : +44(0)20 7946 0382</div>
      <div>email : daniel@corvella.co.uk</div>
    </div>
    <div class="band-bottom"></div>
  </section>

  <section class="card card--back">
    <header class="band-top">
      <div class="web">Web : www.corvella.co.uk</div>
    </header>
    <div class="brand">
      <span class="brand-dot"></span>
      <span class="brand-name">corvella</span>
    </div>
    <div class="band-bottom"></div>
  </section>
</body>
</html>
```